Corvane Capital Business Cards

These are professional business cards that are for my family office.
Put fake emails and phone numbers as of now until I finalize those components. This family office controls my families investments, assets, and future. The cards should be professional.
..
.
.
.
I just uploaded another variation of a logo I would like to see as a business card to I am inbeteen which logo to use

Target Market(s)

business

Industry/Entity Type

business

Contact Information for Business Card

Professional, wealth related, finance related.

Requirements
Must have
• Logo

```html
<!DOCTYPE html>
<html lang="en">
<head>
<meta charset="utf-8">
<title>Corvane Capital Business Cards</title>
<link rel="stylesheet" href="https://fonts.googleapis.com/css2?family=Montserrat:wght@400;500;600&display=swap">
<style>
  :root {
    --backdrop: #e6e2da;
    --card: #181d2b;
    --card-edge: #10141f;
    --ink-light: #f2f3f5;
    --ink-muted: #9c9fa7;
    --ink-soft: #d9dbe0;
    --emblem-line: #2e3a5e;
    --emboss: #262d3f;
  }
  * { margin: 0; padding: 0; box-sizing: border-box; }
  html, body {
    width: 900px;
    height: 1200px;
    overflow: hidden;
    background: var(--backdrop);
  }
  .canvas {
    position: relative;
    width: 900px;
    height: 1200px;
    font-family: "Montserrat", sans-serif;
  }
  .card {
    position: absolute;
    left: 80px;
    width: 742px;
    height: 441px;
    border-radius: 24px;
    background: var(--card);
    box-shadow: 0 10px 24px rgba(16, 20, 31, 0.35);
  }
  .card--front { top: 131px; }
  .card--back { top: 638px; }

  .wordmark {
    position: absolute;
    left: 36px;
    top: 66px;
    font-size: 34px;
    font-weight: 600;
    letter-spacing: 0.5px;
    color: var(--ink-light);
  }
  .holder {
    position: absolute;
    right: 48px;
    top: 52px;
    text-align: right;
  }
  .holder__name {
    font-size: 26px;
    font-weight: 600;
    color: var(--ink-muted);
  }
  .holder__role {
    font-size: 17px;
    font-weight: 400;
    color: var(--ink-soft);
    margin-top: 2px;
  }
  .address {
    position: absolute;
    left: 37px;
    top: 270px;
    font-size: 16px;
    line-height: 20px;
    color: var(--ink-soft);
  }
  .contact-list {
    position: absolute;
    left: 37px;
    top: 330px;
    list-style: none;
    font-size: 16px;
    color: var(--ink-soft);
  }
  .contact-list li {
    display: flex;
    align-items: center;
    height: 28.5px;
  }
  .contact-list svg {
    width: 15px;
    height: 15px;
    margin-right: 10px;
    fill: var(--ink-muted);
  }
  .emblem {
    position: absolute;
    left: 440px;
    top: 158px;
    width: 266px;
    height: 266px;
  }
  .back-wordmark {
    position: absolute;
    left: 0;
    right: 0;
    top: 200px;
    text-align: center;
    font-size: 58px;
    font-weight: 600;
    color: var(--emboss);
  }
</style>
</head>
<body>
<div class="canvas">
  <section class="card card--front">
    <div class="wordmark">Corvane Capital</div>
    <div class="holder">
      <div class="holder__name">Marcus Ellery</div>
      <div class="holder__role">Owner</div>
    </div>
    <address class="address" style="font-style:normal">
      42 Linden Court<br>
      Harrow, NJ 07321 USA
    </address>
    <ul class="contact-list">
      <li>
        <svg viewBox="0 0 24 24" aria-hidden="true"><path d="M6.6 10.8a15.1 15.1 0 0 0 6.6 6.6l2.2-2.2a1 1 0 0 1 1-.25 11.4 11.4 0 0 0 3.6.57 1 1 0 0 1 1 1V20a1 1 0 0 1-1 1A17 17 0 0 1 3 4a1 1 0 0 1 1-1h3.5a1 1 0 0 1 1 1c0 1.25.2 2.45.57 3.57a1 1 0 0 1-.25 1z"/></svg>
        (555)214-0187
      </li>
      <li>
        <svg viewBox="0 0 24 24" aria-hidden="true"><path d="M3 5h18v2l-9 6-9-6z M3 9l9 6 9-6v10H3z"/></svg>
        info@corvanecapital.com
      </li>
      <li>
        <svg viewBox="0 0 24 24" aria-hidden="true"><path d="M12 2a10 10 0 1 0 0 20 10 10 0 0 0 0-20zm6.9 6h-3a15.7 15.7 0 0 0-1.4-3.6A8 8 0 0 1 18.9 8zM12 4c.8 1.2 1.5 2.5 1.9 4h-3.8c.4-1.5 1.1-2.8 1.9-4zM4.3 14a8 8 0 0 1 0-4h3.4a16.5 16.5 0 0 0 0 4zm.8 2h3a15.7 15.7 0 0 0 1.4 3.6A8 8 0 0 1 5.1 16zm3-8h-3a8 8 0 0 1 4.4-3.6A15.7 15.7 0 0 0 8.1 8zM12 20c-.8-1.2-1.5-2.5-1.9-4h3.8c-.4 1.5-1.1 2.8-1.9 4zm2.3-6H9.7a14.7 14.7 0 0 1 0-4h4.6a14.7 14.7 0 0 1 0 4zm.2 5.6a15.7 15.7 0 0 0 1.4-3.6h3a8 8 0 0 1-4.4 3.6zm1.8-5.6a16.5 16.5 0 0 0 0-4h3.4a8 8 0 0 1 0 4z"/></svg>
        www.corvanecapital.com
      </li>
    </ul>
    <svg class="emblem" viewBox="0 0 266 266" aria-hidden="true">
      <circle cx="133" cy="133" r="129" fill="none" stroke="var(--emblem-line)" stroke-width="4"/>
    </svg>
  </section>

  <section class="card card--back">
    <div class="back-wordmark">Corvane Capital</div>
  </section>
</div>
</body>
</html>
```